Quillmarsh Property Solutions need a business card design

Hello guys. We would need a business card design asap please.
We are a start up property investment business based in London UK specialised in buying, selling, managing and letting properties and helping distressed property owners.
The name of our Business is Quillmarsh, the logo symbolises the four fundamental elements of the world (earth, air, fire and water) and so it stands for strength, stability, longevity.
We would like the business card to communicate professionalism and reliability. Many many thanks indeed for your work.

Details:

1.) Rosalind Updike
Property Investor
Mobile: +44(0)7700123456
Email: rosalind.quillmarsh@mailbox-example.com

2.) Dominic Updike
Property Investor
Mobile: +44(0)7700987654
Email: dominic.quillmarsh@mailbox-example.com

```html
<!DOCTYPE html>
<html lang="en">
<head>
<meta charset="utf-8">
<title>Quillmarsh Property Solutions – Business Card</title>
<link rel="stylesheet" href="https://fonts.googleapis.com/css2?family=Josefin+Sans:wght@700&family=Carlito:wght@400&display=swap">
<style>
  :root {
    --page: #d2d2d4;
    --card-dark: #262626;
    --card-light: #ffffff;
    --brand-grey: #b3b3b3;
    --faint-grey: #ededed;
    --red: #d1222b;
    --blue: #2f5fae;
    --green: #1e8a3f;
    --text-light: #ffffff;
    --brand-font: "Josefin Sans", Arial, sans-serif;
    --body-font: "Carlito", "Open Sans", sans-serif;
  }
  * { box-sizing: border-box; margin: 0; padding: 0; }
  html, body { width: 883px; height: 1200px; overflow: hidden; }
  body { background: var(--page); position: relative; font-family: var(--body-font); }

  .card {
    position: absolute; left: 246px; width: 390px;
    overflow: hidden; box-shadow: 0 3px 8px rgba(0,0,0,.25);
  }
  .card--back { top: 380px; height: 218px; background: var(--card-dark); }
  .card--front { top: 615px; height: 204px; background: var(--card-light); }

  .tri-strip { position: absolute; right: 0; bottom: 0; display: flex; height: 11px; width: 171px; }
  .tri-strip span { flex: 1; }
  .tri-strip .green { background: var(--green); }
  .tri-strip .blue { background: var(--blue); }
  .tri-strip .red { background: var(--red); }

  .brand { position: absolute; color: var(--brand-grey); font-family: var(--brand-font); font-weight: 700; text-transform: uppercase; white-space: nowrap; }
  .brand__square { background: var(--brand-grey); flex: none; }
  .brand__name span { display: block; line-height: 1.1; }

  /* Back card: square left, name to the right */
  .card--back .brand { left: 104px; top: 146px; display: flex; align-items: center; gap: 14px; }
  .card--back .brand__square { width: 40px; height: 40px; }
  .card--back .brand__name .line-1 { font-size: 26px; letter-spacing: 1px; }
  .card--back .brand__name .line-2 { font-size: 13px; letter-spacing: 1px; margin-left: 20px; margin-top: 4px; }

  /* Front card: square above, name centred below */
  .card--front .brand { left: 24px; top: 16px; width: 120px; display: flex; flex-direction: column; align-items: center; text-align: center; }
  .card--front .brand__square { width: 50px; height: 50px; margin-bottom: 10px; }
  .card--front .brand__name .line-1 { font-size: 16px; letter-spacing: .5px; }
  .card--front .brand__name .line-2 { font-size: 8px; letter-spacing: .5px; margin-top: 2px; }

  .faint-name {
    position: absolute; left: 158px; top: 34px; transform: rotate(-10deg); transform-origin: left top;
    color: var(--faint-grey); font-family: var(--brand-font); font-weight: 700;
    text-transform: uppercase; white-space: nowrap;
  }
  .faint-name span { display: block; line-height: 1.05; }
  .faint-name .line-1 { font-size: 30px; letter-spacing: 1px; }
  .faint-name .line-2 { font-size: 17px; margin-left: 30px; }

  .contact-panel { position: absolute; left: 0; right: 0; top: 123px; bottom: 0; background: var(--card-dark); }
  .contact-bar { position: absolute; left: 20px; width: 366px; color: var(--text-light); display: flex; align-items: center; padding-left: 14px; white-space: nowrap; }
  .contact-bar--name { top: 7px; height: 23px; background: var(--red); font-size: 14px; }
  .contact-bar--name .role { font-size: 11px; margin-left: 8px; padding-left: 8px; border-left: 1px solid var(--text-light); line-height: 13px; }
  .contact-bar--phone { top: 32px; height: 14px; background: var(--blue); font-size: 11px; }
  .contact-bar--email { top: 48px; height: 14px; background: var(--green); font-size: 11px; }
  .contact-bar svg { width: 9px; height: 9px; margin-right: 8px; flex: none; }
</style>
</head>
<body>

  <section class="card card--back" aria-label="Business card back">
    <div class="brand">
      <span class="brand__square"></span>
      <span class="brand__name"><span class="line-1">Quillmarsh</span><span class="line-2">Property Solutions</span></span>
    </div>
    <div class="tri-strip"><span class="green"></span><span class="blue"></span><span class="red"></span></div>
  </section>

  <section class="card card--front" aria-label="Business card front">
    <div class="faint-name" aria-hidden="true"><span class="line-1">Quillmarsh</span><span class="line-2">Property Solutions</span></div>
    <div class="brand">
      <span class="brand__square"></span>
      <span class="brand__name"><span class="line-1">Quillmarsh</span><span class="line-2">Property Solutions</span></span>
    </div>
    <div class="contact-panel">
      <div class="contact-bar contact-bar--name">Rosalind Updike<span class="role">Property Investor</span></div>
      <div class="contact-bar contact-bar--phone">
        <svg viewBox="0 0 10 10" aria-hidden="true"><rect x="2" y="0.5" width="6" height="9" rx="1" fill="none" stroke="#fff" stroke-width="1"/></svg>
        +44(0)7700123456
      </div>
      <div class="contact-bar contact-bar--email">
        <svg viewBox="0 0 10 10" aria-hidden="true"><rect x="0.5" y="2" width="9" height="6" fill="#fff"/><path d="M0.5 2 L5 5.5 L9.5 2" fill="none" stroke="#1e8a3f" stroke-width="1"/></svg>
        rosalind.quillmarsh@mailbox-example.com
      </div>
      <div class="tri-strip"><span class="green"></span><span class="blue"></span><span class="red"></span></div>
    </div>
  </section>

</body>
</html>
```